Professional Package for CPA Firm

We would like a stationery design for our new CPA Firm based in Atlanta, GA called 'Vale 8'. We work with investors to help grow investments, tax free. We would like the design to have a professional/minimal look with a 'wow' factor. We need 9.5″ x 4.125″, 9x12, and 10x13 mailing envelopes, business cards, and a letterhead. We have a logo that is already complete. For the letterhead, we would like to have space to put credentials at the bottom of the page

Industry/Entity Type

CPA, Accounting

```html
<!DOCTYPE html>
<html lang="en">
<head>
<meta charset="utf-8">
<title>Vale 8 — Stationery</title>
<link rel="stylesheet" href="https://fonts.googleapis.com/css2?family=Montserrat:wght@400;700&family=Open+Sans:wght@400;600;700&family=Roboto:wght@400&display=swap">
<style>
  :root {
    --bg: #ebebeb;
    --paper: #f4f4f4;
    --paper-warm: #f1f1f1;
    --ink: #1a1a1a;
    --body: #4a4a4a;
    --blue: #2a93c6;
    --dark: #1b1b1b;
    --line: #d6d6d6;
  }
  * { margin: 0; padding: 0; box-sizing: border-box; }
  html, body { width: 1200px; height: 795px; overflow: hidden; }
  body { background: var(--bg); position: relative; font-family: "Open Sans", sans-serif; color: var(--body); }

  .sheet { position: absolute; background: var(--paper); }

  /* shared brand lockup */
  .brand { display: flex; flex-direction: column; }
  .brand-row { display: flex; align-items: center; gap: 4px; }
  .brand-mark { background: var(--blue); display: block; }
  .brand-name { font-family: "Montserrat", sans-serif; font-weight: 700; color: var(--ink); line-height: 1; }
  .brand-tag { font-family: "Montserrat", sans-serif; font-weight: 400; color: var(--ink); letter-spacing: .06em; }

  .footer-bar { position: absolute; left: 0; right: 0; bottom: 0; display: flex; gap: 2px; }
  .footer-bar .accent { background: var(--blue); }
  .footer-bar .rule { background: var(--dark); flex: 1; }

  .icon { width: 5px; height: 5px; display: inline-block; vertical-align: -0.5px; margin-right: 2px; }

  /* letterhead */
  .letterhead { left: 293px; top: 99px; width: 292px; height: 415px; }
  .letterhead .brand { position: absolute; left: 25px; top: 30px; }
  .letterhead .brand-mark { width: 9px; height: 9px; }
  .letterhead .brand-name { font-size: 14px; }
  .letterhead .brand-tag { font-size: 4px; margin-top: 2px; }
  .letterhead .contact { position: absolute; left: 190px; top: 30px; font-size: 5.6px; line-height: 7.6px; color: var(--body); }
  .letter-body { position: absolute; left: 25px; top: 97px; width: 241px; font-size: 5.3px; line-height: 8px; text-align: justify; color: var(--body); }
  .letter-body p { margin-bottom: 8px; }
  .signature { width: 36px; height: 34px; background: linear-gradient(135deg, #e4e4e4, #dcdcdc); margin-top: 6px; }
  .letterhead .footer-bar { height: 8px; }
  .letterhead .footer-bar .accent { width: 21px; }

  /* presentation folder */
  .folder { left: 636px; top: 80px; width: 347px; height: 437px; background: var(--paper-warm); }
  .folder-spine { position: absolute; top: 0; bottom: 0; width: 1px; background: var(--line); }
  .folder .brand { position: absolute; left: 0; right: 0; top: 290px; align-items: center; transform: translateY(-50%); }
  .folder .brand-row { gap: 12px; }
  .folder .brand-mark { width: 34px; height: 34px; }
  .folder .brand-name { font-size: 52px; }
  .folder .brand-tag { font-size: 14.5px; letter-spacing: .12em; margin-top: 8px; }
  .folder-url { position: absolute; left: 0; right: 0; top: 399px; text-align: center; font-family: "Roboto", sans-serif; font-size: 11px; color: var(--ink); }
  .folder-url .highlight { color: var(--blue); }

  /* business cards */
  .card { width: 133px; height: 75px; }
  .card-front { left: 187px; top: 551px; }
  .card-front .brand { position: absolute; left: 19px; top: 26px; }
  .card-front .brand-mark { width: 5px; height: 5px; }
  .card-front .brand-name { font-size: 10px; }
  .card-front .brand-tag { font-size: 3px; margin-top: 1px; }
  .card-divider { position: absolute; left: 63px; top: 21px; width: 1px; height: 32px; background: var(--ink); }
  .card-details { position: absolute; left: 70px; top: 21px; font-size: 3.2px; line-height: 4.4px; color: var(--ink); }
  .card-details .person { font-weight: 700; font-size: 4.2px; line-height: 4.6px; }
  .card-details .role { color: var(--blue); font-weight: 600; margin-bottom: 2px; }
  .card-front .footer-bar { height: 4px; gap: 1px; }
  .card-front .footer-bar .accent { width: 14px; }
  .card-back { left: 187px; top: 647px; background: linear-gradient(160deg, #3a3a3a, #242424); }

  /* #10 envelope front */
  .envelope-front { left: 353px; top: 561px; width: 329px; height: 157px; }
  .envelope-front .brand { position: absolute; left: 33px; top: 34px; align-items: center; }
  .envelope-front .brand-mark { width: 9px; height: 9px; }
  .envelope-front .brand-name { font-size: 14px; }
  .envelope-front .brand-tag { font-size: 4px; margin-top: 2px; }
  .envelope-front .return-address { font-family: "Roboto", sans-serif; font-size: 6px; line-height: 7px; text-align: center; color: var(--body); margin-top: 3px; }
  .envelope-front .footer-bar { height: 9px; }
  .envelope-front .footer-bar .accent { width: 24px; }

  /* envelope back */
  .envelope-back { left: 713px; top: 561px; width: 329px; height: 157px; }
  .envelope-flap { position: absolute; left: 0; top: 0; width: 329px; height: 50px; background: var(--dark); clip-path: polygon(0 0, 100% 0, 98% 100%, 2% 100%); }
  .flap-fold { position: absolute; left: 8px; right: 8px; top: 52px; height: 1px; background: var(--line); }
  .envelope-back .brand { position: absolute; left: 0; right: 0; top: 14px; align-items: center; }
  .envelope-back .brand-mark { width: 4px; height: 4px; }
  .envelope-back .brand-name { font-size: 9px; color: #ffffff; }
  .envelope-back .brand-tag { font-size: 2.4px; color: #ffffff; margin-top: 1px; }
</style>
</head>
<body>

  <!-- Letterhead -->
  <section class="sheet letterhead">
    <div class="brand">
      <div class="brand-row"><span class="brand-mark"></span><span class="brand-name">Vale 8</span></div>
      <span class="brand-tag">CPAs and Tax Advisors</span>
    </div>
    <address class="contact" style="font-style:normal">
      48 Cedar Ridge Road,<br>
      Marietta, GA 30060<br>
      <span style="display:block;height:2px"></span>
      <svg class="icon" viewBox="0 0 10 10"><path d="M2 1l2 2-1 1.5c.8 1.4 1.7 2.3 3 3L7.5 6l2 2-1.5 1.5C5 9 1 5 .5 2.5z" fill="#2a93c6"/></svg>+14045550182<br>
      <svg class="icon" viewBox="0 0 10 10"><rect x="0" y="2" width="10" height="6.5" fill="#2a93c6"/><path d="M0 2l5 4 5-4" stroke="#fff" stroke-width="1" fill="none"/></svg>info@valeeight.com<br>
      <svg class="icon" viewBox="0 0 10 10"><circle cx="5" cy="5" r="4.3" stroke="#2a93c6" stroke-width="1.2" fill="none"/><path d="M.7 5h8.6M5 .7c-2.5 2.5-2.5 6 0 8.6M5 .7c2.5 2.5 2.5 6 0 8.6" stroke="#2a93c6" stroke-width=".8" fill="none"/></svg>www.valeeight.com
    </address>
    <div class="letter-body">
      <p>Dear customer,</p>
      <p>Lorem ipsum dolor sit amet, consectetur adipisicing elit, sed do eiusmod tempor incididunt ut labore et dolore magna aliqua. Ut enim ad minim veniam, quis nostrud exercitation ullamco laboris nisi ut aliquip ex ea commodo consequat. Duis aute irure dolor in reprehenderit in voluptate velit esse cillum dolore eu fugiat nulla pariatur. Excepteur sint occaecat cupidatat non proident, sunt in culpa qui officia deserunt mollit anim id est laborum.</p>
      <p>Lorem ipsum dolor sit amet, consectetur adipisicing elit, sed do eiusmod tempor incididunt ut labore et dolore magna aliqua. Ut enim ad minim veniam, quis nostrud exercitation ullamco laboris nisi ut aliquip ex ea commodo consequat. Duis aute irure dolor in reprehenderit in voluptate velit esse cillum dolore eu fugiat nulla pariatur. Excepteur sint occaecat cupidatat non proident, sunt in culpa qui officia deserunt mollit anim id est laborum.</p>
      <p>Lorem ipsum dolor sit amet, consectetur adipisicing elit, sed do eiusmod tempor incididunt ut labore et dolore magna aliqua. Ut enim ad minim veniam, quis nostrud exercitation ullamco laboris nisi ut aliquip ex ea commodo consequat. Duis aute irure dolor in reprehenderit in voluptate velit esse cillum dolore eu fugiat nulla pariatur. Excepteur sint occaecat cupidatat non proident, sunt in culpa qui officia deserunt mollit anim id est laborum.</p>
      <p>Lorem ipsum dolor sit amet, consectetur adipisicing elit, sed do eiusmod tempor incididunt ut labore et dolore magna aliqua. Ut enim ad minim veniam, quis nostrud exercitation ullamco laboris nisi ut aliquip ex ea commodo consequat. Duis aute irure dolor in reprehenderit.</p>
      <p style="margin-bottom:0">Yours Sincerely,</p>
      <div class="signature" role="img" aria-label="Handwritten signature"></div>
    </div>
    <div class="footer-bar"><span class="accent"></span><span class="rule"></span></div>
  </section>

  <!-- Presentation folder -->
  <section class="sheet folder">
    <span class="folder-spine" style="left:4px"></span>
    <span class="folder-spine" style="left:10px"></span>
    <span class="folder-spine" style="left:19px"></span>
    <div class="brand">
      <div class="brand-row"><span class="brand-mark"></span><span class="brand-name">Vale 8</span></div>
      <span class="brand-tag">CPAs and Tax Advisors</span>
    </div>
    <p class="folder-url">www.<span class="highlight">valeeight</span>.com</p>
  </section>

  <!-- Business card, front -->
  <section class="sheet card card-front">
    <div class="brand">
      <div class="brand-row"><span class="brand-mark"></span><span class="brand-name">Vale 8</span></div>
      <span class="brand-tag">CPAs and Tax Advisors</span>
    </div>
    <span class="card-divider"></span>
    <div class="card-details">
      <div class="person">LAURA BENTON</div>
      <div class="role">Managing Director</div>
      48 Cedar Ridge Road,<br>
      Marietta, GA 30060<br>
      <span style="color:var(--blue)">&#9679;</span> +14045550182<br>
      <span style="color:var(--blue)">&#9632;</span> info@valeeight.com<br>
      <span style="color:var(--blue)">&#9675;</span> www.valeeight.com
    </div>
    <div class="footer-bar"><span class="accent"></span><span class="rule"></span></div>
  </section>

  <!-- Business card, back -->
  <section class="sheet card card-back" role="img" aria-label="Dark repeating brand pattern on the card back"></section>

  <!-- Envelope, front -->
  <section class="sheet envelope-front">
    <div class="brand">
      <div class="brand-row"><span class="brand-mark"></span><span class="brand-name">Vale 8</span></div>
      <span class="brand-tag">CPAs and Tax Advisors</span>
      <p class="return-address">48 Cedar Ridge Road,<br>Marietta, GA 30060</p>
    </div>
    <div class="footer-bar"><span class="accent"></span><span class="rule"></span></div>
  </section>

  <!-- Envelope, back -->
  <section class="sheet envelope-back">
    <div class="envelope-flap"></div>
    <span class="flap-fold"></span>
    <div class="brand">
      <div class="brand-row"><span class="brand-mark"></span><span class="brand-name">Vale 8</span></div>
      <span class="brand-tag">CPAs and Tax Advisors</span>
    </div>
  </section>

</body>
</html>
```